Indy Film Production Company/Studio

We need a business card designed from an existing logo. We are a digital studio/production company that caters to creating genre entertainment, like Action, Horror, and martial arts. The card along with the logo will be used to Brand the company from letter heads to banners. The design will also be used for postcards and Brochures. It should be professional and masculine.
Updates

Thank you to all the designers who have participated. I'm narrowing down who it will be. Thank you again.

Target Market(s)

Investors, Networks, Producers, and actors

Industry/Entity Type

Film Production

Contact Information for Business Card

Teodoro Valbuena
Producer/Writer/Director
www.kestrelpicturehouse.example

Requirements
Must have
• Website address, Facebook icon and Twitter icon possibly in the back of the card.
Nice to have
• Logline of Company: Follow The Action.

```html
<!DOCTYPE html>
<html lang="en">
<head>
<meta charset="utf-8">
<title>Kestrel Picture House – Business Card</title>
<link href="https://fonts.googleapis.com/css2?family=Fira+Sans+Condensed:wght@500;800&family=Roboto:wght@400&display=swap" rel="stylesheet">
<style>
  :root {
    --backdrop: #a8a6a6;
    --card: #f3f2f1;
    --brand-red: #c0312b;
    --swoosh: #1f1b1a;
    --ink: #262626;
    --on-red: #ffffff;
  }
  * { margin: 0; padding: 0; box-sizing: border-box; }
  html, body { width: 1200px; height: 1200px; overflow: hidden; }
  body { background: var(--backdrop); position: relative; font-family: "Roboto", sans-serif; }

  .card {
    position: absolute;
    width: 740px;
    height: 420px;
    background: var(--card);
    overflow: hidden;
    box-shadow: 0 10px 24px rgba(0,0,0,0.18);
  }
  .card--front { left: 230px; top: 118px; }
  .card--back  { left: 230px; top: 643px; }

  .brand-name {
    font-family: "Fira Sans Condensed", sans-serif;
    font-weight: 800;
    color: var(--brand-red);
    text-transform: uppercase;
    line-height: 0.98;
  }
  .card--front .brand-name {
    position: absolute;
    left: 0; right: 0; top: 135px;
    text-align: center;
    font-size: 64px;
  }
  .card--back .brand-name {
    position: absolute;
    left: 56px; top: 140px;
    font-size: 44px;
  }

  .back-wave { position: absolute; inset: 0; width: 740px; height: 420px; }

  .holder {
    position: absolute;
    right: 34px; top: 42px;
    text-align: right;
    color: var(--on-red);
  }
  .holder__name {
    font-family: "Fira Sans Condensed", sans-serif;
    font-weight: 500;
    font-size: 27px;
  }
  .holder__role { font-size: 16px; margin-top: 8px; }

  .contact-list {
    position: absolute;
    left: 58px; top: 296px;
    list-style: none;
    color: var(--ink);
    font-size: 18px;
  }
  .contact-list li { display: flex; align-items: center; height: 28.5px; }
  .contact-list svg { width: 16px; height: 16px; margin-right: 14px; fill: var(--brand-red); }

  .address {
    position: absolute;
    right: 28px; top: 326px;
    font-size: 18px;
    line-height: 29px;
    color: var(--ink);
  }
</style>
</head>
<body>

<section class="card card--front" aria-label="Card front">
  <div class="brand-name">Kestrel<br>Picture House</div>
</section>

<section class="card card--back" aria-label="Card back">
  <svg class="back-wave" viewBox="0 0 740 420" aria-hidden="true">
    <path fill="var(--brand-red)" d="M0 0 H740 V196 C660 196 590 170 500 110 C390 40 200 10 0 44 Z"/>
    <path fill="var(--swoosh)" d="M0 56 C170 8 360 22 500 104 C590 158 660 200 740 202 V214 C650 214 580 176 490 122 C360 44 190 28 0 82 Z"/>
  </svg>

  <div class="holder">
    <div class="holder__name">Your Good Name</div>
    <div class="holder__role">Managing Director</div>
  </div>

  <div class="brand-name">Kestrel<br>Picture House</div>

  <ul class="contact-list">
    <li>
      <svg viewBox="0 0 16 16" aria-hidden="true"><path d="M2 6c0-2 3-3 6-3s6 1 6 3v1h-3V6H5v1H2zM4 8h8l1 5H3z"/></svg>
      +00 111 222 3333
    </li>
    <li>
      <svg viewBox="0 0 16 16" aria-hidden="true"><path d="M1 3h14v10H1z M2 4l6 5 6-5" /></svg>
      yourname@yourwebsite.com
    </li>
    <li>
      <svg viewBox="0 0 16 16" aria-hidden="true"><circle cx="8" cy="8" r="7"/><path d="M1 8h14M8 1v14" stroke="#f3f2f1" stroke-width="1.2"/></svg>
      www.yourwebsite.com
    </li>
  </ul>

  <p class="address">Your Long Commercial or<br>business address in 2 line</p>
</section>

</body>
</html>
```